Herbal Apothecary Rebrand

I am in the process of merging two companies Fern Hollow Oils and Under Willow Apothecary. I am dissolving Fern Hollow Oils (FHO) and need to blend a few of the products into the Under Willow Apothecary (UWA) line. These blended products will take on a fresh new look. This is where I need some help. I have a few ideas but need some creative genius to bring them together.
The following products need to be merged and once a logo is agreed upon I will be working with this designer with further pay to create the following:
~ body oils (labels and packaging) **existing product shown in image A-1
~ plant bath medicines (labels and packaging) **a new product with the bottle and packaging shown in images attached
~ facial serum (labels and packaging - the packaging will be the same cardboard boxes used for the body oils) **existing product shown in
image A-2
~ teas (labeling) **a new product - packaging sample pics attached
~ as well as having the ability to carry over into the creation of 40 different essential oil containers. ** An idea I have is shown in image C-1.
Ideas...
I prefer distinct lines, square designs vs circular or curvy. I prefer clean and clear vs busy.
I like the layout shown in images A-1 & A-2 and could see moving forward with a very similar style without the indigenous logo. I would like to see what it looks like to have the UWA logo (building with trees) in place of the indigenous logo. ** I am open to reworking the UWA logo to make it a bit more vertical in size vs being quite small and horizontal. This could include revising or recreating the building and trees altogether.
I like the speckled background (shown in image B-1), it gives the sense that it is aged and goes with the Apothecary theme, however I'm not completely attached to it.
I like the off white labels that I currently have for the BODY OILS and the SERUM and I am leaning towards this as the colour for the new blended line. I would also be open to seeing a lighter version of the turquoise.
This is just an idea that I have however I am open to something completely new. What is important is that it blends nicely with the current line of products available at UWA (the entire line can be seen online). There is a good chance that I will be merging the products over to the new and improved design as we move through the older packaging.
Notes on Plant Bath labels:
**If working from the current layout of the Body Oil labels this can be used as an example to create a template
~ The top will have the new or reworked logo (with or without the company name depending on space available)
~ First line for each bottle will have a name eg: THYME + ROSE
~ Second line will be the purpose of the medicine eg: HEART OPENING
~ The next line will read: PLANT BATH
~Then space for a little blurb eg: BRINGING BALANCE TO THE EMOTIONAL AND ENERGETIC HEALTH OF THE HEART.
~ The size of the bottle will read 400 ML but in a vertical direction on the bottle
Notes on Tea labels:
The teas have not been created yet but I'm looking for some ideas that follow in the same design as the Plant Bath labels so the following can be used as an example:
~ Name; TULSI + ROSE
~ The purpose: ELEVATED HEART
~ The bottom will read: LOOSE TEA
~ Blurb about the benefits: A TRANSFORMATIONAL CREATION OF WARM NOTES WITH DEEP WOODY UNDERTONES. THIS ANYTIME TEA IS AS PLEASING IN THE HEALTH BENEFITS AS IT IS TO THE TASTE.
~ Include the size: 100g
**I maxed out in pictures so I wasn't able to add more inspiration pics but I also quite like the brook & meadow tea line (shows up in a google search) as its clean and clear. The difference being I won't be printing directly on the packaging, it will need to be a label.
Logo Text
I would like to see if we can incorporate the name UNDER WILLOW APOTHECARY however this might make it too busy. Perhaps smaller lettering for "under willow" and larger for "APOTHECARY". It also might be the case that adding this on the front makes things look too busy. I'm open to creative suggestions.

```html
<!DOCTYPE html>
<html lang="en">
<head>
<meta charset="utf-8">
<title>Thyme + Rose Plant Bath Label</title>
<link href="https://fonts.googleapis.com/css2?family=Barlow+Condensed:wght@300;400;500;600&display=swap" rel="stylesheet">
<style>
  :root {
    --ink: #7a2e1e;
    --label: #eeedea;
    --page: #ffffff;
  }
  html, body {
    margin: 0;
    padding: 0;
    width: 900px;
    height: 1200px;
    overflow: hidden;
    background: var(--page);
  }
  .canvas {
    position: relative;
    width: 900px;
    height: 1200px;
  }
  .label {
    position: absolute;
    left: 45px;
    top: 306px;
    width: 809px;
    height: 587px;
    background: var(--label);
    color: var(--ink);
    font-family: "Barlow Condensed", sans-serif;
    overflow: hidden;
  }
  .side-text {
    position: absolute;
    top: 46px;
    height: 496px;
    margin: 0;
    writing-mode: vertical-rl;
    transform: rotate(180deg);
    font-size: 14px;
    line-height: 16px;
    font-weight: 300;
    letter-spacing: 0.2px;
    text-transform: uppercase;
  }
  .side-text strong { font-weight: 600; }
  .usage { left: 43px; width: 50px; }
  .ingredients { left: 106px; width: 16px; }

  .brand {
    position: absolute;
    left: 229px;
    width: 352px;
    top: 40px;
    height: 130px;
    display: flex;
    align-items: center;
    justify-content: center;
    font-size: 22px;
    font-weight: 400;
    letter-spacing: 3px;
    white-space: nowrap;
  }

  .product {
    position: absolute;
    left: 229px;
    width: 352px;
    margin: 0;
    white-space: nowrap;
  }
  .product-name {
    top: 212px;
    font-size: 72px;
    font-weight: 600;
    letter-spacing: -1px;
    line-height: 1;
  }
  .product-type {
    top: 306px;
    font-size: 50px;
    font-weight: 600;
    letter-spacing: 3px;
    line-height: 1;
  }
  .product-origin {
    top: 374px;
    font-size: 45px;
    font-weight: 300;
    letter-spacing: 1.5px;
    line-height: 1;
  }
  .rule {
    position: absolute;
    left: 229px;
    width: 352px;
    height: 2px;
    background: var(--ink);
  }
  .rule-1 { top: 298px; }
  .rule-2 { top: 362px; }
  .rule-3 { top: 440px; }
  .rule-4 { top: 542px; }

  .blurb {
    position: absolute;
    left: 229px;
    top: 454px;
    width: 292px;
    margin: 0;
    font-size: 23px;
    line-height: 25px;
    font-weight: 400;
    letter-spacing: 0.6px;
    text-transform: uppercase;
  }
  .divider {
    position: absolute;
    left: 525px;
    top: 454px;
    width: 2px;
    height: 78px;
    background: var(--ink);
  }
  .volume {
    position: absolute;
    left: 546px;
    top: 454px;
    height: 78px;
    writing-mode: vertical-rl;
    transform: rotate(180deg);
    font-size: 25px;
    font-weight: 600;
    letter-spacing: 2px;
    text-align: center;
  }

  .web-panel {
    position: absolute;
    left: 654px;
    top: 50px;
    width: 118px;
    height: 490px;
    border: 1.5px solid var(--ink);
  }
  .web-address {
    position: absolute;
    left: 742px;
    top: 160px;
    height: 272px;
    writing-mode: vertical-rl;
    transform: rotate(180deg);
    font-size: 23px;
    font-weight: 300;
    letter-spacing: 1.5px;
    white-space: nowrap;
  }
</style>
</head>
<body>
<div class="canvas">
  <section class="label">
    <p class="side-text usage"><strong>Suggested use:</strong> pour a generous capful under warm running water. soak for twenty minutes and breathe deeply. rinse lightly and rest after bathing. may also be used as a soothing foot soak.</p>
    <p class="side-text ingredients"><strong>Ingredients:</strong> sunflower oil, thyme, rose petal, cedar, orange, cardamom organic.</p>

    <div class="brand">UNDER WILLOW APOTHECARY</div>

    <h1 class="product product-name">THYME + ROSE</h1>
    <div class="rule rule-1"></div>
    <h2 class="product product-type">PLANT BATH</h2>
    <div class="rule rule-2"></div>
    <h3 class="product product-origin">ORGANIC BOTANICALS</h3>
    <div class="rule rule-3"></div>

    <p class="blurb">A restorative blend<br>of warm, bright notes<br>with deep earthy undertones.</p>
    <div class="divider"></div>
    <span class="volume">400ML</span>
    <div class="rule rule-4"></div>

    <div class="web-panel"></div>
    <span class="web-address">underwillowapothecary.com</span>
  </section>
</div>
</body>
</html>
```